Yoga/movement guide/teacher for adult yoga practice and kid yoga

What is the positioning or mission statement of your company? to guide individuals in a yoga-based safe and sustainable movement practice applicable to all ages and body types. Currently my focus is working with children in daycare and school settings, but my goal is to expand into private yoga practice for adults, and potentially as part of rented space in studios. I hope to find a way to work with children AND adults (so would love for logo to be appealing to both), but current focus is with children based on need and demand in the community. yoga for children also compliments my backround as a pediatrician/neonatologist, and I greatly miss interacting with children. I also want to emphasize a yoga/movement practice that is focused more on what one feels internally through movement. NOT what one looks like asthetically. I believe in removing all mirrors from yoga/movement practice. It should be an experience of movement/poses/yoga through appropriate cueing and education. It is not about the details of how far the knee should bend, or how high the leg should be. Focusing on foudation first, core, then core engagement and ultimately expression of poses/movements. A focus on strength, stability and mobility, not just flexibility, which is the common perception/association with yoga. I also want individuals to learn to be an advocate of their own health. Through guidance, I hope for individuals to connect with their body so they know themselves so well to be able to advocate for themselves in the modern healthcare world. This internal experience and connection is so essential in a world where modern medicine has become a business and it is all about making a dollar. the connection with patients is lost, and individuals need to learn to empower themselves and through their new found voice to be able to articulate what is wrong.<br/>Does your company have a tagline or slogan that should be included with the logo? "Move With Inner Light"<br/>What do you hope your company can be known for? Accessible yoga for a sustained practice. A guided movement practice where one gains information and knowledge of oneself through a mind/body connection. For one feel good physically with a new awaraness of their internal radiance that exists in all beings. Physical rejuvenation egnites a light and increases energy to flow through the physical body, which ultimately tranlates into works of kindness for others and out in the world. <br/>What color palettes might you prefer? why? love the colors currently chosen<br/>Where will the logo be primarily used? initially business cards, but hopefully future websites, t-shirts, and potentially local magazine adds. Also starting with a small couple of banners for community events in the area. I currently practice as a nomad out of my car :)<br/>Are there any elements you would prefer to see in the logo? Movement. A modern depiction of a human body/figure practicing movement. Hoping to avoid a stereotypical yoga pose per say, just because I want to people to think of it more of a movement practice with yoga roots. Modern yoga. There are elements of breathing and connecting with oneself through the flow of breath and movement, but I do not focus on the meditative/cerebral aspect of the yoga practice. What I teach is almost reaching a meditative state through movement. I personally don't practice, nor resonate with just seated meditation. just not my thing :)<br/>In your opinion, what defines a well-designed logo? curiosity. enough info for individuals to think they know what it means, but want to know more. invokes curiosity, but not too abstract. Reproducible. not too complicated. I want also to invoke a community feel, so a design that appeals to all people within a community. <br/>What is your preference in reference to icons, typography, spokespeople (characters), etc.? modern design. I love the idea of a logo for my purposes, to invoke a sense of movement from within. So not too static. <br/>What words or icons must be included in the logo? movement with yoga roots. <br/>What logos do you like and why? A representation, but not exact. I think some ambiguity is intriguing for others, and also memorable. I want it to be an artistic representation of movement/yoga<br/>What logos do you dislike and why? too busy, too loud. <br/>In your opinion, what is the primary purpose for a logo? association<br/>Who is the primary target audience? (who is most likely to use your services/product?) Children and their parents, but ultimately to expand into teaching adults. I even have aspirations of prenatal and post-natal yoga. Potentially incorporating infants. <br/>Who currently uses your product the most? n/a (working in schools/daycare currently. It is currently all volunteer)<br/>Are you pleased with the range of people your company serves? n/a<br/>Are you looking to expand, modify, or completely change your target audience? or will it remain the same? yes! expand into an adult audience. <br/>How do you plan to focus on your target audience? currently by working through schools and daycares. hopefully ultimately through after school care programs and then offering kid yoga in an existing yoga studio (working on this with Q Studio in Ridgeland, currently)<br/>What are your main forms of advertising? word of mouth, schools, daycares. Happy kids talking to their parents about the yoga class they took and happy teachers :)<br/>How do most customers find out about your company?<br/>Which gender are you targeting? All genders! However, with kid yoga, often the maternal individual in the child's life is more involved with decision making as far as extracurricular activities

Target Market(s)

individuals and families interested in wellness and feeling great

Contact Information for Business Card

Dana Whitford
Yoga Instructor
RYT-200, RCYT

certified yoga teacher for adults and children

Colors

Designer to choose colors to be used in the design.

Requirements
Must have
• "Move With Inner Light"
Nice to have
• logo with same colors

```html
<!DOCTYPE html>
<html lang="en">
<head>
<meta charset="utf-8">
<title>Brightfold Studios – Business Card</title>
<link rel="stylesheet" href="https://fonts.googleapis.com/css2?family=Amatic+SC:wght@400;700&family=Open+Sans:wght@300;400;700&display=swap">
<style>
  :root {
    --backdrop: #d5d5d5;
    --sky: #74d0ea;
    --sun: #ffe050;
    --teal: #5cc6cc;
    --ink: #5a5a5a;
    --paper: #ffffff;
  }
  * { box-sizing: border-box; margin: 0; padding: 0; }
  html, body { width: 1200px; height: 900px; overflow: hidden; }
  body {
    background: var(--backdrop);
    font-family: "Open Sans", sans-serif;
    position: relative;
  }
  .card {
    position: absolute;
    top: 150px;
    width: 340px;
    height: 595px;
    box-shadow: 0 6px 14px rgba(0,0,0,0.22);
    overflow: hidden;
  }
  .card--front { left: 220px; background: var(--sky); }
  .card--back { left: 640px; background: var(--paper); }

  /* front */
  .front-mark {
    position: absolute;
    top: 60px; left: 0; width: 100%;
    display: flex; flex-direction: column; align-items: center; gap: 14px;
  }
  .mark-dot {
    width: 160px; height: 160px; border-radius: 50%;
    background: var(--sun);
  }
  .brand-name {
    font-family: "Open Sans", sans-serif;
    font-weight: 300;
    letter-spacing: 0.02em;
    white-space: nowrap;
  }
  .front-mark .brand-name { font-size: 28px; color: var(--paper); }
  .tagline {
    position: absolute;
    top: 350px; left: 0; width: 100%;
    text-align: center;
    font-family: "Amatic SC", sans-serif;
    font-size: 28px;
    letter-spacing: 0.14em;
    white-space: nowrap;
    color: var(--paper);
  }
  .swirl {
    position: absolute;
    border-radius: 50%;
    background: var(--sun);
  }
  .swirl--e { width: 26px; height: 26px; left: 285px; top: 305px; }
  .swirl--a { width: 34px; height: 34px; left: 40px; top: 425px; }
  .swirl--b { width: 24px; height: 24px; left: 130px; top: 470px; }
  .swirl--c { width: 86px; height: 86px; left: 225px; top: 425px; }
  .swirl--d { width: 150px; height: 150px; left: -40px; top: 505px; }

  /* back */
  .back-mark {
    position: absolute;
    top: 70px; left: 0; width: 100%;
    display: flex; flex-direction: column; align-items: center; gap: 12px;
  }
  .back-mark .mark-dot { width: 110px; height: 110px; }
  .back-mark .brand-name { font-size: 32px; color: var(--ink); }
  .back-tagline {
    font-family: "Amatic SC", sans-serif;
    font-size: 16px;
    letter-spacing: 0.2em;
    white-space: nowrap;
    color: var(--teal);
  }
  .contact {
    position: absolute;
    top: 340px; left: 0; width: 100%;
    text-align: center;
    color: var(--ink);
  }
  .person-name { font-size: 22px; font-weight: 700; color: var(--teal); }
  .person-role { font-size: 16px; margin-top: 2px; }
  .contact-icons {
    display: flex; justify-content: center; gap: 18px;
    margin: 14px 0 8px;
  }
  .contact-icons svg { width: 16px; height: 16px; }
  .contact-line { font-size: 15px; line-height: 1.5; }
  .accent-rule {
    width: 44px; height: 3px;
    background: var(--sun);
    margin: 24px auto 0;
  }
</style>
</head>
<body>

<section class="card card--front" aria-label="Card front">
  <div class="front-mark">
    <span class="mark-dot"></span>
    <span class="brand-name">Brightfold Studios</span>
  </div>
  <div class="swirl swirl--e" role="img" aria-label="Yellow swirl ornament"></div>
  <p class="tagline">Move With Inner Light</p>
  <div class="swirl swirl--a" role="img" aria-label="Yellow swirl ornament"></div>
  <div class="swirl swirl--b" role="img" aria-label="Yellow swirl ornament"></div>
  <div class="swirl swirl--c" role="img" aria-label="Yellow swirl ornament"></div>
  <div class="swirl swirl--d" role="img" aria-label="Large yellow swirl ornament"></div>
</section>

<section class="card card--back" aria-label="Card back">
  <div class="back-mark">
    <span class="mark-dot"></span>
    <span class="brand-name">Brightfold Studios</span>
    <span class="back-tagline">Move With Inner Light</span>
  </div>
  <div class="contact">
    <p class="person-name">Dana Whitford</p>
    <p class="person-role">Founder</p>
    <div class="contact-icons">
      <svg viewBox="0 0 16 16" aria-label="Phone"><path d="M4 1.5 6.5 4 5 6c1 2 3 4 5 5l2-1.5 2.5 2.5-2 2.5C7 14 2 9 1.5 3.5Z" fill="#5cc6cc"/></svg>
      <svg viewBox="0 0 16 16" aria-label="Email"><rect x="1.5" y="3.5" width="13" height="9" fill="none" stroke="#5cc6cc" stroke-width="1.5"/><path d="M1.5 3.5 8 9l6.5-5.5" fill="none" stroke="#5cc6cc" stroke-width="1.5"/></svg>
      <svg viewBox="0 0 16 16" aria-label="Website"><circle cx="8" cy="8" r="6.5" fill="none" stroke="#5cc6cc" stroke-width="1.5"/><path d="M1.5 8h13M8 1.5c-3 3.5-3 9.5 0 13M8 1.5c3 3.5 3 9.5 0 13" fill="none" stroke="#5cc6cc" stroke-width="1.2"/></svg>
    </div>
    <p class="contact-line">601-555-0142</p>
    <p class="contact-line">danawhitford@mailbox.com</p>
    <p class="contact-line">www.brightfoldstudios.com</p>
    <div class="accent-rule"></div>
  </div>
</section>

</body>
</html>
```